Cleaning service website design

We need a new nice web design(logo will be the same) for a new cleaning service Company:

Informations about Company and logo you can take from flyers in attachments.

This is a cleaning service Company which have simple rules and we would like to show that(in checklist form) on website:

- What we do and that we're Cleaning Green

- Why us?

- How much(our pricing is simple)

Also we would like to communicate with clients by some nice/big pictures on website and the most important thing is our phone number and short/fast Brimtallow.

Also there should be some space for description about our Company.

Generally all information on main page can be short: about us, about service(what we do), last reviews, tips (for example: Tip of the week) and other can be some introduction to subpage where will be more information.

There will be few subpages like: About us, About our service, Photos(Before and after), Reviews , Tips, FAQ, Contact, Looking for a Job? - most of them will be just text so you can project just one example.

```html
<!DOCTYPE html>
<html lang="en">
<head>
<meta charset="utf-8">
<title>Tidy Nest – House Cleaning</title>
<link rel="stylesheet" href="https://fonts.googleapis.com/css2?family=Open+Sans:ital,wght@0,400;0,600;0,700;1,400&family=PT+Sans+Narrow:wght@700&family=Yanone+Kaffeesatz:wght@400&display=swap">
<style>
:root{
  --green:#6aab1e;
  --green-dark:#4f8a12;
  --blue:#1a5fa8;
  --orange:#f58a0b;
  --orange-dark:#e2620a;
  --red:#e11d1d;
  --ink:#222;
  --muted:#666;
  --line:#d8d8d8;
  --footer:#2b2b2b;
  --footer-base:#1c1c1c;
}
*{box-sizing:border-box;margin:0;padding:0}
html,body{width:800px;height:1200px;overflow:hidden;background:#fff}
body{font-family:"Open Sans",sans-serif;color:var(--ink)}
.page{width:960px;height:1440px;position:relative;transform:scale(.833333);transform-origin:0 0}
.abs{position:absolute}

/* header */
.header{left:0;top:0;width:960px;height:103px;border-bottom:3px solid #ececec}
.brand{left:119px;top:26px;display:flex;align-items:center;gap:12px}
.brand-dot{width:34px;height:34px;border-radius:50%;background:var(--green)}
.brand-name{font-size:30px;font-weight:700;color:var(--green)}
.callout{right:120px;top:10px;text-align:right;font-size:11px}
.callout b{font-weight:700}
.callout .phone{display:flex;align-items:center;justify-content:flex-end;gap:6px;font-size:21px;font-weight:700;margin-top:1px}
.nav{left:324px;top:53px;display:flex;font-family:"PT Sans Narrow",sans-serif;font-size:12px;text-transform:uppercase}
.nav a{display:block;height:50px;padding:18px 0 0;margin-right:27px;color:var(--ink);text-decoration:none}
.nav a.active{background:#f1f1f1;color:var(--green);padding:18px 11px 0;border-bottom:4px solid var(--green);margin-right:15px}

/* hero */
.hero{left:0;top:107px;width:960px;height:403px;background:linear-gradient(90deg,#2f5b1c 0%,#6f8e4a 40%,#a5b68a 55%,#4e7a2a 80%,#2e5a18 100%)}
.hero-figure{left:510px;top:148px;width:450px;height:362px;background:radial-gradient(ellipse at 55% 60%,#9aa04a 0%,#6b7530 50%,rgba(60,90,30,0) 75%)}
.hero-title{left:119px;top:146px;color:#fff;font-size:33px;font-weight:400;letter-spacing:.5px}
.hero-title b{font-weight:700}
.hero-sub{left:119px;top:182px;color:#fff;font-size:18px;font-weight:600}
.hero-sub .price{color:var(--red);font-size:32px;font-weight:700;vertical-align:-3px}
.checks{left:119px;top:228px;list-style:none;color:#fff;font-size:12px}
.checks li{display:flex;align-items:center;height:26.8px;gap:9px}
.checks svg{flex:none}
.cta{left:119px;top:408px;width:197px;height:46px;border-radius:4px;background:linear-gradient(#ffa31a,var(--orange-dark));color:#fff;font-size:20px;font-weight:700;display:flex;align-items:center;justify-content:center;gap:10px}
.badge{left:340px;top:400px;width:56px;height:56px;border-radius:50%;background:radial-gradient(circle at 40% 35%,#fff,#cfe9a6 55%,#6fb52a)}

/* cards */
.card{top:540px;height:272px;border:1px solid var(--line);background:#fff;box-shadow:0 8px 6px -6px rgba(0,0,0,.15)}
.card-photo{margin:3px 3px 0;height:86px}
.card h3{font-family:"Open Sans",sans-serif;font-weight:400;font-size:15px;color:var(--green);text-align:center;margin:10px 0 14px}
.bullets{list-style:none;font-size:10.5px;padding:0 16px 0 22px}
.bullets li{position:relative;padding-left:16px;margin-bottom:9px;line-height:15px}
.bullets li::before{content:"";position:absolute;left:2px;top:5px;width:5px;height:5px;background:#333}
.pricing{font-size:10.5px;padding:0 20px 0 30px;line-height:18.5px}
.pricing .g{color:var(--green)}
.pricing a{color:var(--blue)}
.pricing .note{font-style:italic;font-size:9px;margin-top:18px}
.estimate h3{font-size:16px;margin:14px 0 12px}
.field{height:22px;border:1px solid #cfcfcf;margin:0 24px 12px;font-size:8px;color:#999;padding:6px 9px}
.field-row{display:flex;gap:12px;margin:0 24px 12px}
.field-row .field{margin:0;flex:1}
.est-foot{display:flex;justify-content:space-between;align-items:flex-end;margin:14px 24px 0}
.est-foot small{display:block;font-size:8px;font-weight:700}
.est-foot b{font-size:14px;color:var(--blue)}
.submit{width:66px;height:21px;background:linear-gradient(#ff8c1a,var(--orange-dark));color:#fff;font-size:9px;font-weight:700;display:flex;align-items:center;justify-content:center}

/* about */
.about{left:119px;top:848px;width:721px;height:114px;border:1px solid var(--line);background:linear-gradient(#fff,#f4f4f4)}
.about-photo{left:2px;top:-18px;width:177px;height:130px;background:linear-gradient(160deg,#b8a089,#3a3a42 60%,#1f2630)}
.about h2{position:absolute;left:187px;top:16px;font-family:"Yanone Kaffeesatz",sans-serif;font-weight:400;font-size:26px;color:var(--green)}
.about p{position:absolute;left:187px;top:48px;width:520px;font-size:9.6px;line-height:15px}
.about .more{position:absolute;right:16px;top:80px;font-size:8px;color:var(--green)}

/* review + tip */
.lower{left:119px;top:993px;width:721px;height:198px;border:1px solid var(--line)}
.lower h3{position:absolute;font-weight:600;font-size:15px;color:var(--green)}
.reviewer{left:16px;top:70px;width:110px;height:126px;background:linear-gradient(#e9d7bf,#c9a77f 45%,#1d1d22 70%)}
.bubble{left:106px;top:44px;width:283px;height:104px;border:1px solid #ccc;border-radius:3px;background:#fff;padding:10px 12px;font-size:9px}
.bubble .who b{font-weight:700}
.bubble .who span{color:#888;margin-left:14px}
.bubble p{font-style:italic;color:#333;line-height:15px;margin:6px 0 5px;padding-bottom:5px;border-bottom:1px dotted #bbb}
.meta{display:flex;gap:9px;font-size:8px;align-items:center}
.meta .stars{color:var(--red);letter-spacing:-1px;font-size:9px}
.meta a{color:var(--blue);text-decoration:none}
.btn-more{width:74px;height:19px;background:linear-gradient(#8cbf3c,var(--green-dark));color:#fff;font-size:9px;display:flex;align-items:center;justify-content:center}
.divider{left:433px;top:50px;width:1px;height:120px;background:linear-gradient(#fff,#ccc,#fff)}
.tip-title{left:461px;top:54px;font-size:11px;font-weight:600;color:var(--blue);text-decoration:underline}
.tip-text{left:461px;top:78px;width:236px;font-size:9.6px;line-height:15px}

/* footer */
.footer{left:0;top:1220px;width:960px;height:188px;background:var(--footer);color:#fff}
.footer h4{position:absolute;top:32px;font-size:12.5px;font-weight:600}
.footer ul{position:absolute;top:58px;list-style:none;font-size:9px;line-height:18.7px}
.newsletter p{position:absolute;left:556px;top:58px;font-size:9px}
.email{left:556px;top:78px;width:244px;height:32px;background:#fff;border-radius:2px;color:#333;font-size:9px;padding:10px 12px}
.go{left:805px;top:78px;width:34px;height:32px;background:var(--orange);border-radius:2px;font-size:11px;font-weight:700;display:flex;align-items:center;justify-content:center}
.social{left:556px;top:138px;display:flex;gap:7px}
.social span{width:18px;height:18px;border-radius:2px}
.foot-brand{left:760px;top:128px;display:flex;align-items:center;gap:6px}
.foot-brand i{width:16px;height:16px;border-radius:50%;background:var(--green)}
.foot-brand b{font-size:15px;color:var(--green)}
.base{left:0;top:1408px;width:960px;height:32px;background:var(--footer-base);color:#555;font-size:9px;padding:11px 120px}
</style>
</head>
<body>
<div class="page">

  <header class="header abs">
    <div class="brand abs"><span class="brand-dot"></span><span class="brand-name">Tidy Nest</span></div>
    <div class="callout abs">
      <div><b>Call Us</b> to arrange your cleaning on</div>
      <div class="phone">
        <svg width="16" height="18" viewBox="0 0 16 18"><path d="M4 1 L7 5 L5 7 Q6 11 10 13 L12 11 L15 14 L13 17 Q3 15 1 3 Z" fill="var(--blue)"/></svg>
        555-014-2290
      </div>
    </div>
    <nav class="nav abs">
      <a class="active">Home</a><a>About Us</a><a>Our Services</a><a>Photos</a><a>Reviews</a><a>Tips</a><a>Careers</a><a>FAQ</a><a>Contact</a>
    </nav>
  </header>

  <section class="hero abs" role="img" aria-label="Misty green forest path background"></section>
  <div class="hero-figure abs" role="img" aria-label="Woman in a green dress with arms spread wide, breathing fresh air"></div>
  <h1 class="hero-title abs">SIMPLIFY <b>YOUR LIFE</b></h1>
  <p class="hero-sub abs">and some there House Cleaning from <span class="price">$79</span></p>
  <ul class="checks abs">
    <li><svg width="17" height="17" viewBox="0 0 17 17"><circle cx="8.5" cy="8.5" r="8" fill="var(--green)"/><path d="M4.5 8.5 L7.5 11.5 L12.5 5.5" stroke="#fff" stroke-width="2" fill="none"/></svg>Locally Owned &amp; Operated</li>
    <li><svg width="17" height="17" viewBox="0 0 17 17"><circle cx="8.5" cy="8.5" r="8" fill="var(--green)"/><path d="M4.5 8.5 L7.5 11.5 L12.5 5.5" stroke="#fff" stroke-width="2" fill="none"/></svg>Reliable &amp; Affordable</li>
    <li><svg width="17" height="17" viewBox="0 0 17 17"><circle cx="8.5" cy="8.5" r="8" fill="var(--green)"/><path d="M4.5 8.5 L7.5 11.5 L12.5 5.5" stroke="#fff" stroke-width="2" fill="none"/></svg>All Supplies Provided</li>
    <li><svg width="17" height="17" viewBox="0 0 17 17"><circle cx="8.5" cy="8.5" r="8" fill="var(--green)"/><path d="M4.5 8.5 L7.5 11.5 L12.5 5.5" stroke="#fff" stroke-width="2" fill="none"/></svg>No Contracts</li>
    <li><svg width="17" height="17" viewBox="0 0 17 17"><circle cx="8.5" cy="8.5" r="8" fill="var(--green)"/><path d="M4.5 8.5 L7.5 11.5 L12.5 5.5" stroke="#fff" stroke-width="2" fill="none"/></svg>Pet Friendly</li>
    <li><svg width="17" height="17" viewBox="0 0 17 17"><circle cx="8.5" cy="8.5" r="8" fill="var(--green)"/><path d="M4.5 8.5 L7.5 11.5 L12.5 5.5" stroke="#fff" stroke-width="2" fill="none"/></svg>Green Cleaning</li>
  </ul>
  <div class="cta abs">GET STARTED
    <svg width="22" height="18" viewBox="0 0 22 18"><path d="M0 6 H12 V0 L22 9 L12 18 V12 H0 Z" fill="#fff"/></svg>
  </div>
  <div class="badge abs" role="img" aria-label="Green cleaning badge"></div>

  <article class="card abs" style="left:119px;width:230px">
    <div class="card-photo" role="img" aria-label="Smiling family with their dog on a sofa" style="background:linear-gradient(90deg,#c9a67a,#e6cfa9 50%,#8b6a48)"></div>
    <h3>What do we clean?</h3>
    <ul class="bullets">
      <li>Thoroughly clean your bathrooms, kitchen, bedrooms and living areas</li>
      <li>Mop or vacuum your floors</li>
      <li>Dust surfaces</li>
      <li>Collect garbage</li>
      <li>Make beds</li>
    </ul>
  </article>

  <article class="card abs" style="left:364px;width:230px">
    <div class="card-photo" role="img" aria-label="Family relaxing together at home" style="background:linear-gradient(90deg,#e8dccb,#d2b697 55%,#9a8470)"></div>
    <h3>Pricing is..simple</h3>
    <div class="pricing">
      <div><span class="g">$79</span> for homes less than 1000 sq ft</div>
      <div><span class="g">$89</span> for homes 1000-1800 sq ft</div>
      <div><span class="g">$99</span> for homes 1800-2600 sq ft</div>
      <div style="line-height:14px;margin-top:3px">If your home is larger than 2600 sq ft please <a>call for a quote</a></div>
      <div class="note">*rates are for regular service*</div>
    </div>
  </article>

  <article class="card estimate abs" style="left:609px;width:231px">
    <h3>Quick Free Estimate</h3>
    <div class="field">Name</div>
    <div class="field">E-mail</div>
    <div class="field">Postal Code</div>
    <div class="field">Phone</div>
    <div class="field-row"><div class="field">No. of Bathrooms</div><div class="field">No. of Bedrooms</div></div>
    <div class="est-foot">
      <div><small>CALL US TODAY</small><b>555-014-2290</b></div>
      <div class="submit">SUBMIT</div>
    </div>
  </article>

  <section class="about abs">
    <div class="about-photo abs" role="img" aria-label="Portrait of the two company owners"></div>
    <h2>About Tidy Nest.com</h2>
    <p>It's about caring, not just cleaning. Having personally experienced the struggles of finding quality maid service for our home, we want to make it simpler for families in the Brookfield area. Our goal is to provide caring, consistent and reliable house cleaning to every customer we serve.</p>
    <span class="more">READ MORE...</span>
  </section>

  <section class="lower abs">
    <h3 style="left:22px;top:16px">Featured Review</h3>
    <div class="reviewer abs" role="img" aria-label="Portrait of a smiling customer"></div>
    <div class="bubble abs">
      <div class="who"><b>Dana Corwell, Brookfield</b><span>1 review</span></div>
      <p>I had to move out of a rental property and didn't want to hassle with the cleaning, so I called Tidy Nest whom quoted me over the phone and did a brilliant job.</p>
      <div class="meta"><span class="stars">★★★★★</span><span>09/07/2013</span><a>COMMENT</a><a>REPORT</a><a>Share</a><span>HELPFUL?</span></div>
    </div>
    <div class="btn-more abs" style="left:314px;top:164px">View more &gt;</div>
    <div class="divider abs"></div>
    <h3 style="left:461px;top:16px">Tip of the Week</h3>
    <div class="tip-title abs">Cleaning up after your dog or cat</div>
    <p class="tip-text abs">For millions of dog and cat owners, Fido and Fluffy aren't just pets – they're part of the family.<br>But as much as we love our four-legged friends, they sure can .....</p>
    <div class="btn-more abs" style="left:616px;top:164px">View more &gt;</div>
  </section>

  <footer class="footer abs">
    <h4 style="left:119px">Quick Links</h4>
    <ul style="left:121px"><li>Home</li><li>About Us</li><li>Our Service</li><li>Photos</li><li>Contact</li></ul>
    <h4 style="left:264px">Useful Links</h4>
    <ul style="left:264px"><li>Terms of use</li><li>Privacy Policy</li><li>Help Center</li><li>Community</li><li>Login Area</li></ul>
    <h4 style="left:393px">Join Our Community</h4>
    <ul style="left:394px"><li>Friendbook</li><li>Chirper</li><li>ProLink</li></ul>
    <div class="newsletter">
      <h4 style="left:556px">SignUp For Our Monthly Newsletter</h4>
      <p>Subscribe our newsletter &amp; get the latest news &amp; updates</p>
    </div>
    <div class="email abs">Email Address</div>
    <div class="go abs">GO</div>
    <div class="social abs"><span style="background:#3b5ea8"></span><span style="background:#3aa7de"></span><span style="background:#f2a21a"></span></div>
    <div class="foot-brand abs"><i></i><b>Tidy Nest</b></div>
  </footer>
  <div class="base abs">© 2013 by. Tidy Nest. All Rights Reserved.</div>

</div>
</body>
</html>
```